Brightmoor Leaf is a bridge for the people who drink tea to connect with the people who make the tea and the environment in which it is grown.

As a start-up, Brightmoor Leaf needs to establish a fluently persuasive brand image that articulates its unique mission to the up-market tea drinker.

Our passion for high quality tea and our respect for people are boundless. But our budget is shoe-string. Still, we will allocate a disproportionate amount to evolving a brand; including logo, labeling, and packaging, and hope this initial effort will lead to a long-term relationship with a designer. The Brightmoor label, as a component of the brand, must deny the commodity image of tea by broadcasting the uniquely flavorful, healthful, and relaxing experience of drinking tea.

The logo is an image of a liquor pouring from above into a stylized outline of a cup and gracefully folding over on itself within the cup. The image is an echo of video clips that will be featured on the Product page of the ecommerce site. Our initial thought is for the liquor and cup to be white on a rich blue background. But you may have a better idea.

The label must fit a seamless tin canister 4" in diameter; 2" high with a "window" in the lid. There are really three distinct parts to the label: a) wrap-around for the body of the tin; b) a distinct piece to be applied underneath the tin; and c) security strip (s) that connect the lid and the bottom of the tin. The wrap-around must include the following components: the logo, the brand name 'Brightmoor Leaf', the name of the specific tea and space for the following characteristics of the tea: Tea / Garden Name, Harvest Date, Tasting Notes, Weight, Location, and Caffeine content. The piece to be affixed underneath the tin should accommodate Ingredients, Brewing Instructions, and contact details for Brightmoor Leaf. The security strip(s) should be an integral part of the overall visual.

The color scheme should be expandable, i.e.; different colors for different teas.
We are thinking about rich and bold colors. But am eager to see what inspires you!

A very rough proto-type is captured in the attached files.

Target Market(s)

Ages 25 to 45 in densely populated areas of the U.S. and Canada will an above average house-hold income and an interest in what they eat / drink.

Industry/Entity Type

Environment

Requirements
Must have
• 1. Three separate pieces: 1) wrap around for the body of the tin; 2) piece to be affixed to the bottom of the body of the tin; 3) security strip (s). A word about strips: am unsure about one vs two because, two will add to overhead and processing while one will block the view of the contents. Maybe you know how to resolve.
2. clean, crisp lines
3. uncluttered
Nice to have
• 1. a color scheme to accommodate up to 30 different teas. Do not fall into the trap of incorporating the color green on the label for a 'green tea' and yellow for a lemon flavored tea. That approach is limited and has been overdone.
2. a color scheme that, as it expands to accommodate 30 teas, also is anchored by a brand color set. In other words, all labels include a recognizable color set.
3. express the level of caffeine via a gauge or metric
Should not have
• photo images,

```html
<!DOCTYPE html>
<html lang="en">
<head>
<meta charset="utf-8">
<title>Brightmoor Leaf – Tin Label</title>
<link href="https://fonts.googleapis.com/css2?family=Roboto+Condensed:wght@700&family=Lato:wght@400&display=swap" rel="stylesheet">
<style>
  :root{
    --paper:#ffffff;
    --frame:#5a7396;
    --navy:#1f4a7a;
    --royal:#0b4f9c;
    --cyan:#00a2c9;
    --sky:#8dd3e6;
    --mist:#a6dcec;
    --ink:#1f4a7a;
  }
  html,body{margin:0;padding:0;overflow:hidden;background:var(--paper);}
  .canvas{position:relative;width:1200px;height:807px;overflow:hidden;background:var(--paper);}
  .canvas-frame{position:absolute;left:1px;top:1px;width:1187px;height:796px;border:1px solid var(--frame);box-sizing:border-box;}
  .label-art{position:absolute;left:0;top:0;}
  .brand-name{
    position:absolute;margin:0;
    font-family:"Roboto Condensed",sans-serif;font-weight:700;
    color:var(--navy);letter-spacing:0.5px;white-space:nowrap;line-height:1;
  }
  .label-title{left:372px;top:134px;font-size:46px;}
  .lockup-name{left:218px;top:630px;font-size:48px;}
  .lockup-square{position:absolute;left:82px;top:618px;width:104px;height:104px;background:var(--royal);}
  .tea-details{
    position:absolute;left:381px;top:309px;margin:0;padding:0;list-style:none;
    font-family:"Lato",sans-serif;font-variant:small-caps;font-size:12px;
    letter-spacing:1.3px;color:var(--ink);
  }
  .tea-details li{position:relative;height:18px;line-height:14px;}
  .tea-details .colon{position:absolute;left:106px;}
  .caffeine-word{
    position:absolute;left:590px;top:433px;transform-origin:0 0;transform:rotate(-90deg);
    font-family:"Lato",sans-serif;font-variant:small-caps;font-size:9px;letter-spacing:1px;color:var(--ink);
  }
</style>
</head>
<body>
<div class="canvas">
  <div class="canvas-frame"></div>

  <svg class="label-art" width="1200" height="807" viewBox="0 0 1200 807" aria-hidden="false">
    <defs>
      <linearGradient id="title-band" x1="0" y1="0" x2="0" y2="1">
        <stop offset="0" stop-color="#2cb6d8"/>
        <stop offset="1" stop-color="#00a0c8"/>
      </linearGradient>
      <radialGradient id="swirl-glow" cx="0.55" cy="0.4" r="0.7">
        <stop offset="0" stop-color="#b9e6f2"/>
        <stop offset="0.6" stop-color="#8dd3e6"/>
        <stop offset="1" stop-color="#4f9ec6"/>
      </radialGradient>
    </defs>

    <!-- label body -->
    <rect x="346" y="68" width="787" height="394" fill="var(--navy)"/>
    <rect x="346" y="90" width="455" height="7" fill="var(--cyan)"/>
    <rect x="346" y="101" width="420" height="102" fill="url(#title-band)"/>
    <rect x="346" y="230" width="787" height="8" fill="var(--cyan)" opacity="0.5"/>

    <!-- details panel -->
    <rect x="369" y="245" width="764" height="191" fill="var(--sky)"/>
    <rect x="369" y="245" width="400" height="22" fill="var(--mist)"/>
    <path d="M369 267 H598 L710 345 L592 282 H369 Z" fill="var(--cyan)"/>
    <rect x="369" y="282" width="230" height="16" fill="var(--mist)"/>
    <rect x="369" y="298" width="82" height="6" fill="var(--navy)"/>
    <rect x="369.5" y="304.5" width="219" height="131" fill="var(--sky)" stroke="var(--navy)"/>

    <!-- caffeine gauge -->
    <g stroke="var(--navy)" stroke-width="1">
      <rect x="593.5" y="305.5" width="8" height="8" fill="none"/>
      <rect x="593.5" y="318.5" width="8" height="8" fill="none"/>
      <rect x="593.5" y="331.5" width="8" height="8" fill="var(--navy)"/>
      <rect x="593.5" y="344.5" width="8" height="8" fill="var(--navy)"/>
      <rect x="593.5" y="357.5" width="8" height="8" fill="var(--navy)"/>
      <rect x="593.5" y="370.5" width="8" height="8" fill="var(--navy)"/>
    </g>

    <!-- brand square -->
    <rect x="668" y="217" width="92" height="92" fill="var(--royal)"/>

    <!-- pouring liquor illustration area -->
    <path role="img" aria-label="Illustration of tea liquor pouring and folding over itself"
          d="M880 68 H1133 V436 H800 C760 380 748 300 770 220 C790 140 830 90 880 68 Z"
          fill="url(#swirl-glow)"/>
  </svg>

  <h1 class="brand-name label-title">BRIGHTMOOR LEAF</h1>

  <ul class="tea-details">
    <li>Hervest Date<span class="colon">:</span></li>
    <li>Weight<span class="colon">:</span></li>
    <li>Garden<span class="colon">:</span></li>
    <li>Location<span class="colon">:</span></li>
    <li>Testing Note<span class="colon">:</span></li>
  </ul>
  <span class="caffeine-word">Caffeine</span>

  <div class="lockup-square"></div>
  <p class="brand-name lockup-name">BRIGHTMOOR LEAF</p>
</div>
</body>
</html>
```